Varnel Corporate Website for technological company

We need a modern website to promote our product and services.
You can found the actually website at the address: www.varnel-example.ch

We are a new company for B2B market. We would like do show our high precision and innovation capability.

we need a section were is possible to easily upload "news" and documents for our customers.

Target Market(s)

B2B services in the industry market

Industry/Entity Type

It Company

Coding

Coded - Design and coding required

Number of Pages Required

5+ page

Font styles to use
Other font styles liked:
• We accept propositions

Requirements
Must have
• Easy to maintain
• Presentation of the Varnel company
• Presentation of Varnel services and products
• The customer can download our ducumentation
Nice to have
• Sexy and modern

```html
<!DOCTYPE html>
<html lang="en">
<head>
<meta charset="utf-8">
<title>Varnel Sàrl – Intelligent motion</title>
<link href="https://fonts.googleapis.com/css2?family=Open+Sans:ital,wght@0,300;0,400;0,600;0,700;1,400&family=Cinzel:wght@400&display=swap" rel="stylesheet">
<style>
:root{
  --dark:#3b3939;
  --darker:#2f2d2d;
  --gold:#a89b5c;
  --gold-light:#c4b47a;
  --text:#333;
  --muted:#777;
  --line:#e6e6e6;
  --white:#fff;
}
*{margin:0;padding:0;box-sizing:border-box}
html,body{width:746px;height:1200px;overflow:hidden}
body{position:relative;font-family:"Open Sans",sans-serif;color:var(--text);background:var(--white);font-size:7px}
.abs{position:absolute}

/* top bar */
.topbar{left:0;top:0;width:746px;height:18px;background:var(--dark);color:#ddd;font-size:6.5px}
.topbar .item{position:absolute;top:5px;display:flex;align-items:center;gap:4px}
.topbar svg{width:6px;height:6px;fill:var(--gold)}
.lang{position:absolute;left:565px;top:2px;width:60px;height:14px;border:1px solid #555;background:#2c2a2a;color:#eee;padding:3px 5px;font-size:6.5px}
.restricted{position:absolute;left:630px;top:2px;width:55px;height:14px;background:var(--gold);color:#fff;padding:3px 7px;font-size:6.5px}

/* header */
.header{left:0;top:18px;width:746px;height:60px;background:var(--white);border-bottom:1px solid var(--line)}
.brand{position:absolute;left:62px;top:20px;display:flex;align-items:center;gap:6px}
.brand .mark{width:16px;height:16px;background:var(--gold)}
.brand .name{font-weight:700;font-size:18px;letter-spacing:1px;color:#222}
.nav{position:absolute;top:27px;left:282px;font-size:7.5px;font-weight:600;color:#555}
.nav span{position:absolute;white-space:nowrap}

/* hero */
.hero{left:0;top:78px;width:746px;height:324px;
  background:
    radial-gradient(ellipse 90px 140px at 375px 60px, rgba(40,40,42,.75), transparent 70%),
    radial-gradient(ellipse 130px 60px at 400px 30px, rgba(60,120,190,.55), transparent 75%),
    radial-gradient(ellipse 120px 130px at 650px 170px, rgba(235,235,235,.9), transparent 70%),
    radial-gradient(ellipse 110px 90px at 470px 270px, rgba(245,245,245,.85), transparent 70%),
    radial-gradient(ellipse 140px 200px at 60px 200px, rgba(70,70,70,.6), transparent 75%),
    linear-gradient(180deg,#b9b9b9 0%,#d6d6d6 40%,#a9a9a9 75%,#c8c8c8 100%)}
.hero-caption{left:62px;top:251px;width:288px;height:83px;background:rgba(40,38,36,.82);border-left:3px solid var(--gold);padding:14px 0 0 17px}
.hero-caption h2{color:var(--gold-light);font-size:17px;font-weight:600;letter-spacing:.5px}
.hero-caption p{color:#eee;font-size:8px;line-height:14px;margin-top:5px;width:255px}
.dots{left:357px;top:352px;display:flex;gap:3px}
.dots i{width:5px;height:5px;border-radius:50%;background:#ddd;display:block}

/* welcome card */
.card{left:62px;top:367px;width:623px;height:286px;background:var(--white);box-shadow:0 0 8px rgba(0,0,0,.12)}
.tile{position:absolute;left:14px;width:190px;height:122px;border-radius:3px;overflow:hidden}
.tile .photo{position:absolute;inset:0}
.tile .label{position:absolute;left:0;bottom:0;width:100%;height:28px;background:rgba(20,20,20,.75);color:#fff;font-weight:700;font-size:8.5px;padding:9px 10px;display:flex;justify-content:space-between}
.tile .label i{width:8px;height:8px;border-radius:50%;background:var(--gold);display:block}
.welcome{position:absolute;left:236px;top:20px;width:370px}
.welcome .bar{position:absolute;left:0;top:0;width:3px;height:48px;background:var(--gold)}
.welcome h3{margin-left:17px;font-size:11px;font-weight:700;color:#222;letter-spacing:.2px}
.welcome h1{margin-left:17px;font-size:28px;font-weight:300;color:var(--gold);margin-top:2px}
.welcome p{margin-left:17px;font-size:7px;line-height:14.5px;color:var(--muted);margin-top:10px}
.welcome p:first-of-type{margin-top:14px}
.btn{position:absolute;left:251px;top:230px;width:171px;height:39px;background:var(--gold);color:#fff;padding:7px 13px;border-bottom:2px solid #8c7f44}
.btn b{display:block;font-size:9px;font-weight:700;letter-spacing:.2px}
.btn span{font-size:6.5px;opacity:.9}

/* services row */
.service{position:absolute;top:676px;display:flex;gap:11px}
.service .icon{width:36px;height:36px;border-radius:50%;background:var(--gold);flex:none;display:flex;align-items:center;justify-content:center}
.service .icon svg{width:18px;height:18px;stroke:#fff;fill:none;stroke-width:1.6}
.service h4{font-size:9px;font-weight:700;color:#222;margin-top:4px}
.service p{font-size:6.5px;line-height:13.5px;color:var(--muted);margin-top:5px;width:132px}
.chev{position:absolute;top:698px;color:#aaa;font-size:14px;font-weight:300}
.divider{left:90px;top:760px;width:566px;height:2px;background:radial-gradient(ellipse at center,rgba(0,0,0,.1),transparent 70%)}

/* news & testimonials */
.sec-title{position:absolute;top:799px;font-size:12px;font-weight:700;color:#222}
.sec-title::after{content:"";position:absolute;left:0;top:22px;width:32px;height:2px;background:var(--gold)}
.news{position:absolute;left:62px;display:flex;gap:14px}
.news .thumb{width:33px;height:33px;flex:none}
.news h5{font-size:7px;font-weight:700;color:#222;line-height:11.5px;width:110px}
.news span{font-size:6.5px;color:var(--muted)}
.promo{left:237px;top:797px;width:183px;height:167px;
  background:
    radial-gradient(ellipse 50px 60px at 95px 60px, rgba(180,170,160,.7), transparent 75%),
    radial-gradient(ellipse 45px 70px at 140px 45px, rgba(150,145,140,.7), transparent 75%),
    linear-gradient(90deg,rgba(230,232,234,.9) 0%,transparent 30%),
    linear-gradient(180deg,#c9cbcd 0%,#8c8c8c 40%,#3d3d3f 72%,#1f1f20 100%)}
.promo .small{position:absolute;left:14px;top:112px;font-family:"Cinzel",serif;color:var(--gold-light);font-size:11px}
.promo .big{position:absolute;left:14px;top:124px;font-family:"Cinzel",serif;color:var(--gold-light);font-size:20px}
.promo p{position:absolute;left:16px;top:151px;color:#eee;font-size:6.5px;font-style:italic}
.arrows{left:664px;top:801px;color:#aaa;font-size:8px;letter-spacing:3px}
.testi{position:absolute;left:450px;display:flex;gap:13px}
.testi .avatar{width:54px;height:54px;border-radius:50%;background:radial-gradient(circle at 50% 40%,#d9cdbf 0%,#b5a89a 45%,#6a635c 100%);flex:none}
.testi h6{font-size:7px;font-weight:700;color:#222}
.testi h6 em{font-style:normal;font-weight:400;color:var(--gold)}
.testi p{font-size:6.5px;line-height:13.5px;font-style:italic;color:var(--muted);margin-top:3px;width:170px}

/* footer */
.footer{left:0;top:1006px;width:746px;height:164px;background:var(--dark);color:#bbb}
.fcol{position:absolute;top:26px}
.fcol h6{font-size:8px;font-weight:700;color:#fff;margin-bottom:8px}
.fcol li{list-style:none;font-size:6.5px;line-height:13.8px}
.contact li{display:flex;align-items:center;gap:6px;line-height:14.8px}
.contact li i{width:5px;height:6px;background:var(--gold);display:block;border-radius:1px}
.social{display:flex;gap:6px;margin-top:8px}
.social i{width:17px;height:17px;border-radius:50%;background:var(--gold);display:block}
.fbrand{position:absolute;left:570px;top:104px;display:flex;align-items:center;gap:6px}
.fbrand .mark{width:14px;height:14px;background:var(--gold)}
.fbrand .name{font-weight:700;font-size:15px;color:#fff;letter-spacing:1px}
.bottom{left:0;top:1170px;width:746px;height:30px;background:var(--darker);color:#aaa;font-size:6.5px;display:flex;align-items:center;justify-content:center;gap:14px}
</style>
</head>
<body>

<div class="abs topbar">
  <div class="item" style="left:62px"><svg viewBox="0 0 10 10"><path d="M5 0a3.5 3.5 0 0 0-3.5 3.5C1.5 6 5 10 5 10s3.5-4 3.5-6.5A3.5 3.5 0 0 0 5 0z"/></svg>Chemin des Vergers 8 CH - 1600 Montclar</div>
  <div class="item" style="left:243px"><svg viewBox="0 0 10 10"><path d="M2 0l2 2.5-1 1.5c.7 1.4 1.6 2.3 3 3l1.5-1L10 8l-1.5 2C4 9.5.5 6 0 1.5z"/></svg>Call Us : +41 (0)21 555 01 10</div>
  <div class="item" style="left:382px"><svg viewBox="0 0 10 10"><path d="M0 2h10v6H0z"/></svg>Email Us : info@varnel-example.ch</div>
  <div class="lang">English&nbsp;&nbsp;&nbsp;⌄</div>
  <div class="restricted">Restricted ⌄</div>
</div>

<header class="abs header">
  <div class="brand"><span class="mark"></span><span class="name">VARNEL Sàrl</span></div>
  <nav class="nav">
    <span style="left:0">HOME</span>
    <span style="left:58px">SERVICES ⌄</span>
    <span style="left:127px">PRODUCTS ⌄</span>
    <span style="left:203px">EXAMPLES</span>
    <span style="left:278px">DOWNLOAD</span>
    <span style="left:359px">CONTACTS</span>
  </nav>
</header>

<section class="abs hero" role="img" aria-label="Close-up of a CNC milling machine cutting an aluminium part with blue coolant hoses"></section>
<div class="abs hero-caption">
  <h2>INTELLIGENT MOTION</h2>
  <p>The ever-increasing complexity in modern systems, the search for reliability and performance</p>
</div>
<div class="abs dots"><i></i><i></i><i></i><i></i></div>

<section class="abs card">
  <div class="tile" style="top:13px">
    <div class="photo" role="img" aria-label="Motor driver test bench with optical lenses" style="background:radial-gradient(ellipse 60px 40px at 120px 55px,rgba(200,205,215,.55),transparent 75%),radial-gradient(ellipse 70px 50px at 60px 30px,rgba(110,110,110,.6),transparent 75%),linear-gradient(135deg,#5c5c5c 0%,#2a2a2a 55%,#121212 100%)"></div>
    <div class="label">MOTOR DRIVER <i></i></div>
  </div>
  <div class="tile" style="top:148px">
    <div class="photo" role="img" aria-label="Linear actuator module on a blue background" style="background:radial-gradient(ellipse 90px 25px at 110px 55px,rgba(25,25,30,.75),transparent 75%),radial-gradient(ellipse 80px 60px at 40px 20px,rgba(120,175,230,.7),transparent 75%),linear-gradient(135deg,#4d8fd0 0%,#2a6aad 50%,#173f70 100%)"></div>
    <div class="label">BUS INTERFACE <i></i></div>
  </div>
  <div class="welcome">
    <span class="bar"></span>
    <h3>WELCOME TO VARNEL</h3>
    <h1>Intelligent motion</h1>
    <p>The ever-increasing complexity in modern systems, the search for reliability and performance and the continuous desire to reduce production costs and dimensions of the products require a rigorous integration between the electronic units, software and mechanical systems.</p>
    <p>VARNEL Ltd. designs systems in which electronics, software and mechanics are perfectly integrated to achieve uncompromising performance.</p>
    <p>VARNEL Ltd. can develop complete solutions or intervene at a later stage of the product development to carry out studies and / or produce units that will be integrated into your processes, machines or products.</p>
  </div>
  <div class="btn"><b>DOWNLOAD OUR BROCHURE</b><span>Brochure Varnel (EN) [446 kB] ➜</span></div>
</section>

<div class="chev" style="left:36px">〈</div>
<div class="service" style="left:62px">
  <div class="icon"><svg viewBox="0 0 20 20"><circle cx="10" cy="10" r="6"/><circle cx="10" cy="10" r="2.5"/></svg></div>
  <div><h4>VARNEL SERVICES</h4><p>Our prospective clients are the whole range of SMEs, as well as research and development offices...</p></div>
</div>
<div class="service" style="left:275px">
  <div class="icon"><svg viewBox="0 0 20 20"><rect x="5" y="6" width="10" height="8" rx="1"/><path d="M10 3v3M4 17h12"/></svg></div>
  <div><h4>SIMULATION AND MODELING</h4><p>Through a multi-physics modelling approach, Varnel Ltd. can integrate into the simulation all the main elements...</p></div>
</div>
<div class="service" style="left:498px">
  <div class="icon"><svg viewBox="0 0 20 20"><rect x="3" y="4" width="8" height="6" rx="3" transform="rotate(40 7 7)"/><rect x="9" y="10" width="8" height="6" rx="3" transform="rotate(40 13 13)"/></svg></div>
  <div><h4>ELECTRONICS</h4><p>VARNEL Sàrl being active in all fields associated with actuator electronics, can develop solutions integrating...</p></div>
</div>
<div class="chev" style="left:697px">〉</div>
<div class="abs divider"></div>

<h2 class="sec-title" style="left:62px">LATEST NEWS</h2>
<div class="news" style="top:834px"><div class="thumb" role="img" aria-label="Motor component" style="background:radial-gradient(circle at 60% 60%,#e0a030 0%,#b06a20 35%,#1e1e1e 80%)"></div><div><h5>ADDED NEW APPLICATION NOTES</h5><span>Posted on 10 June 2016</span></div></div>
<div class="news" style="top:884px"><div class="thumb" role="img" aria-label="Circuit board" style="background:radial-gradient(circle at 40% 40%,#c9d2c0 0%,#7f9a72 45%,#3d5a3e 100%)"></div><div><h5>ADDED NEW APPLICATION NOTES</h5><span>Posted on 10 June 2016</span></div></div>
<div class="news" style="top:933px"><div class="thumb" role="img" aria-label="Stator winding" style="background:radial-gradient(circle at 50% 50%,#f0e6dc 0%,#c8803e 40%,#4a3020 100%)"></div><div><h5>ADDED NEW APPLICATION NOTES</h5><span>Posted on 10 June 2016</span></div></div>

<div class="abs promo" role="img" aria-label="Two businessmen reviewing a document">
  <span class="small">VARNEL LTD</span>
  <span class="big">DOWNLOAD</span>
  <p>For more information click on the desired file.</p>
</div>

<h2 class="sec-title" style="left:447px">TESTIMONIALS</h2>
<div class="abs arrows">‹ ›</div>
<div class="testi" style="top:834px"><div class="avatar" role="img" aria-label="Portrait of a client"></div><div><h6>MARCO LENZ <em>( Business man )</em></h6><p>Lorem Ipsum is simply dummy text of the printing and typesetting industry has been the industry typesetting industry has been the industry...</p></div></div>
<div class="testi" style="top:905px"><div class="avatar" role="img" aria-label="Portrait of a client"></div><div><h6>MARCO LENZ <em>( Business man )</em></h6><p>Lorem Ipsum is simply dummy text of the printing and typesetting industry has been the industry typesetting industry has been the industry...</p></div></div>

<footer class="abs footer">
  <div class="fcol" style="left:70px"><h6>WELCOME</h6><ul><li>Home</li><li>Services</li><li>Products</li><li>Examples</li><li>Download</li><li>Contacts</li><li>Restricted</li></ul></div>
  <div class="fcol" style="left:171px"><h6>SERVICES</h6><ul><li>VARNEL Services</li><li>Simulation and modeling</li><li>Electronics</li><li>Mechanics</li><li>Software</li></ul></div>
  <div class="fcol" style="left:304px"><h6>PRODUCTS</h6><ul><li>Motor driver</li><li>Tern</li><li>Kiro</li><li>Bus interface</li><li>Alpenar</li></ul></div>
  <div class="fcol contact" style="left:421px"><h6>CONTACT INFO</h6><ul>
    <li style="color:#fff">VARNEL LTD</li>
    <li>Chemin des Vergers 8</li>
    <li>CH - 1600 Montclar</li>
    <li><i></i>+41 (0)21 555 01 10</li>
    <li><i></i>+41 (0)79 555 02 20</li>
    <li><i></i>+41 (0)78 555 03 30</li>
    <li><i></i>info@varnel-example.ch</li>
  </ul></div>
  <div class="fcol" style="left:570px"><h6>FOLLOW US</h6><ul><li>Connect with our social network</li></ul><div class="social"><i></i><i></i><i></i><i></i></div></div>
  <div class="fbrand"><span class="mark"></span><span class="name">VARNEL Sàrl</span></div>
</footer>
<div class="abs bottom"><span>© 2016. VARNEL Ltd. All rights reserved.</span><span>Terms &amp; Conditions</span><span>/</span><span>Privacy Policy</span><span>/</span><span>Disclaimer</span></div>

</body>
</html>
```